Business Card Design Project

We are not a new company, but renamed to "Vantorin Kitchens" last year. We specialize in modern high-end cabinetry imports. We would like to communicate a sense of quality and cutting edge technology. Ideally the design would incorporate our logo colors, silver, red and preferably a black, matte background. Though we are open to suggestions.
Logo is attached.
Edit: I have attached rough drafts of the previous cards, this way you will have all necessary content that needs to go on the cards.
Updates
Project Deadline Extended
Reason: We have received a lot of great designs, but due to the sheer number we couldn't respond to all. We will extend the deadline for another 7 days to finalize and provide feedback to designers.
Thank you for your hard work!
Industry/Entity Type
Business
Look and feel
Each slider illustrates characteristics of the customer's brand and the style your logo design should communicate.

```html
<!DOCTYPE html>
<html lang="en">
<head>
<meta charset="utf-8">
<title>Vantorin Kitchens – Business Cards</title>
<link rel="stylesheet" href="https://fonts.googleapis.com/css2?family=Arimo:wght@400;700&display=swap">
<style>
  :root {
    --stage: #8a5e3b;
    --label: #1e1a16;
    --card-top: #262626;
    --card-bottom: #141414;
    --card-deep: #070707;
    --silver: #c9c9c9;
    --accent-red: #d8262b;
    --ink: #ffffff;
    --rule: #5a5a5a;
    --dots-light: #5c5c5c;
  }
  * { margin: 0; padding: 0; box-sizing: border-box; }
  html, body { width: 1200px; height: 788px; overflow: hidden; }
  body {
    position: relative;
    background: var(--stage);
    font-family: "Arimo", Arial, sans-serif;
    color: var(--ink);
  }
  .view-label {
    position: absolute;
    width: 200px;
    text-align: center;
    font-size: 20px;
    color: var(--label);
  }
  .card {
    position: absolute;
    width: 525px;
    height: 299px;
    border-radius: 22px;
    overflow: hidden;
    background: linear-gradient(180deg, var(--card-top), var(--card-bottom));
    box-shadow: 0 4px 10px rgba(0,0,0,.45);
  }
  .card--deep { background: var(--card-deep); }
  .brand {
    position: absolute;
    display: flex;
    align-items: center;
    gap: 12px;
    color: var(--silver);
    font-weight: 700;
    text-transform: uppercase;
    letter-spacing: 2px;
    white-space: nowrap;
  }
  .brand__mark {
    display: inline-block;
    background: var(--silver);
  }
  .brand--front { left: 26px; top: 92px; font-size: 25px; }
  .brand--front .brand__mark { width: 22px; height: 22px; }
  .brand--center { left: 0; right: 0; justify-content: center; top: 132px; font-size: 30px; }
  .brand--center .brand__mark { width: 26px; height: 26px; }
  .holder {
    position: absolute;
    left: 25px;
    top: 207px;
    font-size: 17px;
    font-weight: 700;
    text-transform: uppercase;
  }
  .holder__title {
    font-size: 13px;
    font-weight: 400;
    text-transform: none;
    margin-left: 4px;
  }
  .rule {
    position: absolute;
    left: 25px;
    right: 17px;
    top: 234px;
    height: 1px;
    background: var(--rule);
  }
  .contact {
    position: absolute;
    top: 244px;
    font-size: 12.5px;
    line-height: 18px;
  }
  .contact b { font-weight: 700; }
  .contact--office { left: 25px; }
  .contact--direct { left: 165px; }
  .contact--address { right: 17px; text-align: right; }
  .texture {
    position: absolute;
    background: radial-gradient(ellipse at center, var(--dots-light) 0%, #222 55%, transparent 80%);
  }
  .texture--top { left: 0; top: 0; width: 290px; height: 90px; }
  .texture--bottom { right: 0; bottom: 0; width: 260px; height: 95px; }
</style>
</head>
<body>
  <div class="view-label" style="left:207px; top:22px;">front</div>
  <div class="view-label" style="left:790px; top:22px;">front-1</div>
  <div class="view-label" style="left:214px; top:405px;">back</div>
  <div class="view-label" style="left:790px; top:405px;">Back - 1</div>

  <section class="card" style="left:53px; top:63px;">
    <div class="brand brand--front"><span class="brand__mark"></span>Vantorin Kitchens</div>
    <div class="holder">Marek Dolan,<span class="holder__title">President</span></div>
    <div class="rule"></div>
    <div class="contact contact--office"><b>p</b> : 555.201.0148<br><b>f</b>&nbsp; : 555.201.0177</div>
    <div class="contact contact--direct"><b>c</b> : 555.310.4426<br><b>e</b> : marek@vantorinkitchens.ca</div>
    <div class="contact contact--address">1280 - 48 Ave.<br>Lakeford, AB T0X 2K4</div>
  </section>

  <section class="card" style="left:637px; top:63px;">
    <div class="brand brand--front"><span class="brand__mark"></span>Vantorin Kitchens</div>
    <div class="holder">Tobias Dolan,<span class="holder__title">Director</span></div>
    <div class="rule"></div>
    <div class="contact contact--office"><b>p</b> : 555.201.0148<br><b>f</b>&nbsp; : 555.201.0177</div>
    <div class="contact contact--direct"><b>c</b> : 555.318.9052<br><b>e</b> : tobias@vantorinkitchens.ca</div>
    <div class="contact contact--address">1280 - 48 Ave.<br>Lakeford, AB T0X 2K4</div>
  </section>

  <section class="card" style="left:57px; top:447px;">
    <div class="brand brand--center"><span class="brand__mark"></span>Vantorin Kitchens</div>
  </section>

  <section class="card card--deep" style="left:625px; top:446px;">
    <div class="texture texture--top" role="img" aria-label="Perforated metal texture"></div>
    <div class="texture texture--bottom" role="img" aria-label="Perforated metal texture"></div>
    <div class="brand brand--center"><span class="brand__mark"></span>Vantorin Kitchens</div>
  </section>
</body>
</html>
```